For Sale

Need 36 x 20 hanging sign for real estate post. I like the dana whitcombe sample. My logo is Cedar Ridge Living and Property Team and I work for Lumora realty. I do specialize in luxury and regular residential sales. if you can use qr code or the website below. can you add mls and realtor log small on bottom. logo
Margaret Pellonquist
o: (888) 555-0174 ext 4821
c: (516) 555-0139
margaretpellonquist@lumorarealty.com

```html
<!DOCTYPE html>
<html lang="en">
<head>
<meta charset="utf-8">
<title>For Sale – Margaret Pellonquist</title>
<link href="https://fonts.googleapis.com/css2?family=Open+Sans:wght@300;400;600;700;800&display=swap" rel="stylesheet">
<style>
  :root {
    --backdrop: #3f3f3f;
    --navy: #0a3a8c;
    --navy-deep: #062b66;
    --slate: #5c5c5c;
    --paper: #ffffff;
    --paper-shade: #e7e9ea;
    --ink: #1c2442;
    --white: #ffffff;
  }
  * { margin: 0; padding: 0; box-sizing: border-box; }
  html, body {
    width: 929px; height: 1200px; overflow: hidden;
    background: var(--backdrop);
    font-family: "Open Sans", sans-serif;
  }
  .sign {
    position: absolute; left: 75px; top: 384px;
    width: 778px; height: 432px; overflow: hidden;
  }
  .sign-shapes { position: absolute; inset: 0; }
  .brand {
    position: absolute; left: 290px; top: 36px;
    display: flex; align-items: center; gap: 12px;
    color: var(--ink);
  }
  .brand-mark { width: 30px; height: 30px; border-radius: 50%; background: var(--ink); }
  .brand-rule { width: 1.5px; height: 50px; background: var(--ink); }
  .brand-name { font-weight: 400; line-height: 1.1; }
  .brand-name .line-1 { display: block; font-size: 30px; letter-spacing: 0.3px; }
  .brand-name .line-2 { display: block; font-size: 10px; font-weight: 700; letter-spacing: 6px; margin-top: 3px; }
  .headline {
    position: absolute; right: 80px; top: 172px; text-align: right; color: var(--white);
  }
  .headline .for-sale { font-size: 64px; font-weight: 700; line-height: 1; letter-spacing: 0.5px; }
  .headline .mobile {
    display: flex; align-items: center; justify-content: flex-end; gap: 6px;
    font-size: 37px; font-weight: 700; margin-top: 8px; line-height: 1;
  }
  .headline .mobile svg { width: 28px; height: 28px; }
  .agent-name {
    position: absolute; left: 36px; top: 330px;
    color: var(--white); font-weight: 300; font-size: 38px; line-height: 1.1;
  }
  .divider { position: absolute; width: 1px; background: var(--white); opacity: 0.85; }
  .divider.name-split { left: 254px; top: 374px; height: 34px; }
  .divider.badge-split { left: 538px; top: 362px; height: 50px; }
  .contact { position: absolute; left: 277px; top: 361px; color: var(--white); }
  .contact-row { display: flex; align-items: center; gap: 6px; }
  .contact-row .dot {
    width: 16px; height: 16px; border-radius: 50%; border: 1.5px solid var(--white);
    display: flex; align-items: center; justify-content: center;
  }
  .contact-row .dot svg { width: 9px; height: 9px; }
  .contact-row.office { font-size: 17px; font-weight: 600; }
  .contact-row.email { font-size: 11.5px; font-weight: 600; margin-top: 6px; }
  .badges { position: absolute; left: 552px; top: 369px; display: flex; gap: 4px; }
  .badge { border: 1.5px solid var(--white); }
  .badge.small { width: 28px; height: 36px; }
  .badge.wide { width: 52px; height: 26px; margin-top: 10px; }
  .brokerage {
    position: absolute; left: 646px; top: 366px; width: 85px;
    color: var(--white); font-weight: 700; font-size: 22px; line-height: 1; text-align: center;
  }
  .brokerage .sub { display: block; font-size: 10px; letter-spacing: 3px; margin-top: 3px; }
</style>
</head>
<body>
  <main class="sign">
    <svg class="sign-shapes" viewBox="0 0 778 432" width="778" height="432">
      <defs>
        <linearGradient id="paperGradient" x1="0" y1="0" x2="1" y2="0.4">
          <stop offset="0" stop-color="var(--paper)"/>
          <stop offset="1" stop-color="var(--paper-shade)"/>
        </linearGradient>
        <radialGradient id="portraitGradient" cx="0.5" cy="0.45" r="0.6">
          <stop offset="0" stop-color="#c9a594"/>
          <stop offset="0.55" stop-color="#6b4a3c"/>
          <stop offset="1" stop-color="#e6e8e8"/>
        </radialGradient>
      </defs>
      <rect class="paper" width="778" height="432" fill="url(#paperGradient)"/>
      <path class="lower-band" d="M0 272 C 80 240 190 222 300 218 L 778 230 L 778 432 L 0 432 Z" fill="var(--slate)"/>
      <path class="wave-edge" d="M 262 220 C 360 194 470 110 590 103 C 680 98 745 134 778 166 L 778 275 C 730 315 660 345 590 345 C 480 345 380 250 262 222 Z" fill="var(--navy-deep)"/>
      <path class="wave" d="M 262 222 C 360 202 470 124 590 117 C 680 112 745 148 778 182 L 778 275 C 730 315 660 345 590 345 C 480 345 380 250 262 222 Z" fill="var(--navy)"/>
      <circle class="portrait-ring" cx="155" cy="181" r="122" fill="var(--navy-deep)"/>
      <circle class="portrait" cx="155" cy="181" r="112" fill="url(#portraitGradient)" role="img" aria-label="Portrait photo of agent Margaret Pellonquist"/>
    </svg>

    <div class="brand">
      <span class="brand-mark"></span>
      <span class="brand-rule"></span>
      <span class="brand-name">
        <span class="line-1">CEDAR RIDGE LIVING</span>
        <span class="line-2">AND PROPERTY TEAM</span>
      </span>
    </div>

    <div class="headline">
      <div class="for-sale">FOR SALE</div>
      <div class="mobile">
        <svg viewBox="0 0 24 24" aria-hidden="true"><path fill="#fff" d="M6.6 10.8a15 15 0 0 0 6.6 6.6l2.2-2.2a1 1 0 0 1 1-.25 11.4 11.4 0 0 0 3.6.57 1 1 0 0 1 1 1V20a1 1 0 0 1-1 1A17 17 0 0 1 3 4a1 1 0 0 1 1-1h3.5a1 1 0 0 1 1 1c0 1.250.2 2.450.57 3.57a1 1 0 0 1-.25 1z"/><path fill="none" stroke="#fff" stroke-width="1.8" d="M14 3.5a7 7 0 0 1 6.5 6.5M14 7a3.5 3.5 0 0 1 3 3"/></svg>
        <span>(516) 555-0139</span>
      </div>
    </div>

    <div class="agent-name">Margaret<br>Pellonquist</div>
    <span class="divider name-split"></span>

    <div class="contact">
      <div class="contact-row office">
        <span class="dot"><svg viewBox="0 0 10 10"><rect x="1" y="1" width="8" height="8" rx="1" fill="#fff"/></svg></span>
        <span>(888) 555-0174 ext 4821</span>
      </div>
      <div class="contact-row email">
        <span class="dot"><svg viewBox="0 0 10 10"><rect x="0.5" y="2" width="9" height="6" fill="#fff"/><path d="M0.5 2 L5 5.5 L9.5 2" stroke="#5c5c5c" fill="none"/></svg></span>
        <span>margaretpellonquist@lumorarealty.com</span>
      </div>
    </div>

    <span class="divider badge-split"></span>
    <div class="badges">
      <span class="badge small"></span>
      <span class="badge wide"></span>
    </div>

    <div class="brokerage">Lumora<span class="sub">REALTY</span></div>
  </main>
</body>
</html>
```